Web Design for guards MMJ transport and security services

Harbor Crest Protective solutions a tallow unified company, is looking for a designer to create a website that displays our service portfolio. We need marketing pictures and content to be created in a original and competitive fashion, intriguing to our customers. We will need forms on the website to be created for calendar booking (somehow integrate into exchange if possible) and general inquiry forms. There will need to be pages dedicated to our staff, MMJ trasnport & Courier services, our vehicles, alarm systems, video systems, video monitoring, private investigations, and surveillance aduit and compliance investigations, payment gateway integration, and general company information. I Have attached our main company logo. Also have a emphasis on being state licensed by the Colorado RPB. Have a link to our parent site, tallowcctv.example

Target Market(s)

Colorado Marijuana industry, MMJ transport services, guard services, armed gaurd services.

Contact Information for Business Card

Would like a sleek simple design highlighting what we offer. must match the website and have a overall professional straight to the point appearance.

Number of Pages Required

1 page

Colors
33b8a4
00a990
9bcb3c
acd036
cadf82
85cae6
33a6d7
0792cd

Requirements
Must have
• Easy to use, lots of images, professional.
Nice to have
• Creativity

```html
<!DOCTYPE html>
<html lang="en">
<head>
<meta charset="utf-8">
<title>Harbor Crest Protective Solutions</title>
<link rel="stylesheet" href="https://fonts.googleapis.com/css2?family=Open+Sans:wght@400;600;700&family=Montserrat:wght@500;600;700&family=Exo+2:wght@600;700&display=swap">
<style>
:root{
  --red:#e1232b;
  --red-dark:#b9171e;
  --ink:#333333;
  --muted:#6d6d6d;
  --dark:#262626;
  --charcoal:#3a3a3a;
  --line:#e2e2e2;
  --blue:#1f8fd1;
  --green:#8cc63f;
  --lime:#a9d334;
  --pale:#f3f4f6;
  --white:#ffffff;
}
*{box-sizing:border-box;margin:0;padding:0}
html,body{width:1200px;height:2651px;overflow:hidden}
body{position:relative;background:var(--white);font-family:"Open Sans",Arial,sans-serif;color:var(--ink)}
.abs{position:absolute}
p{font-size:12.5px;line-height:22px;color:var(--muted)}

/* header */
.top-strip{left:495px;top:0;width:705px;height:53px;background:var(--charcoal);clip-path:polygon(0 0,100% 0,100% 100%,40px 100%)}
.top-strip ul{list-style:none;display:flex;justify-content:flex-end;padding:19px 40px 0 0}
.top-strip li{color:var(--white);font-family:"Montserrat",sans-serif;font-size:11.5px;font-weight:500;padding:0 16px;border-left:1px solid #888;line-height:13px}
.top-strip li:first-child{border-left:none}
.brand{left:88px;top:44px;display:flex;align-items:center;gap:10px}
.brand .mark{width:36px;height:36px;border-radius:50%;background:var(--red)}
.brand span{font-family:"Montserrat",sans-serif;font-weight:700;font-size:22px;color:var(--red)}
.socials{left:642px;top:74px;display:flex;gap:10px}
.socials i{display:block;width:32px;height:32px;border:1.5px solid #d6d6d6;border-radius:50%;background:#fafafa}
.search{left:866px;top:71px;width:248px;height:39px;border:1px solid #d8d8d8;display:flex;align-items:center;justify-content:space-between;padding:0 14px;font-size:12px;color:#777}
.nav{left:0;top:127px;width:1200px;height:55px;background:linear-gradient(var(--red),var(--red-dark));border-bottom:3px solid #f0f0f0}
.nav ul{list-style:none;display:flex;padding-left:85px;height:100%}
.nav li{color:var(--white);font-family:"Montserrat",sans-serif;font-size:12px;font-weight:500;padding:0 13.5px;display:flex;align-items:center;height:100%}
.nav li.active{background:#444;padding:0 17px}

/* hero */
.hero{left:0;top:182px;width:1200px;height:518px;
  background:
    linear-gradient(90deg,rgba(20,24,30,0) 45%,rgba(20,24,30,.75) 70%,rgba(20,24,30,.8) 100%),
    radial-gradient(ellipse 260px 230px at 300px 150px,#b58a6c 0%,#8a6a55 40%,rgba(60,55,50,0) 100%),
    radial-gradient(ellipse 520px 330px at 280px 470px,#1c2635 0%,#202a38 55%,rgba(30,36,44,0) 100%),
    linear-gradient(180deg,#6f7663 0%,#4e5649 35%,#3a4048 70%,#2b3038 100%)}
.hero-title{left:680px;top:318px;font-family:"Exo 2",sans-serif;font-weight:700;font-size:34px;line-height:44px;text-transform:uppercase;color:var(--white);letter-spacing:.5px}
.hero-title b{color:var(--lime);font-weight:700}
.hero-copy{left:680px;top:421px;width:480px;color:#e8e8e8;font-size:12.5px;line-height:23px}
.btn-green{left:680px;top:527px;width:221px;height:49px;background:var(--green);color:var(--white);font-family:"Montserrat",sans-serif;font-size:12px;font-weight:600;display:flex;align-items:center;justify-content:center;gap:8px;border-radius:3px}
.dots{left:1026px;top:663px;display:flex;gap:6px}
.dots i{width:12px;height:12px;border:2px solid #fff;border-radius:50%}
.dots i.on{border-color:var(--green)}

/* section headings */
.sec-head{left:0;width:1200px;display:flex;justify-content:center;align-items:center;gap:12px;font-family:"Montserrat",sans-serif;font-weight:600;font-size:22px;color:var(--charcoal);text-transform:uppercase}
.sec-head .mark{width:30px;height:30px;border:3px solid var(--red);border-radius:50%}
.sec-head em{font-style:normal;color:var(--red)}
.sec-intro{left:205px;width:790px;text-align:center}

/* service cards */
.card{width:330px;height:168px;border:2px solid var(--line);background:var(--white)}
.card svg{position:absolute;left:16px;top:20px}
.card h3{position:absolute;left:84px;top:18px;font-family:"Montserrat",sans-serif;font-weight:600;font-size:14.5px;color:var(--charcoal)}
.card p{position:absolute;left:84px;top:44px;width:228px;font-size:11.5px;line-height:23px}
.card a{position:absolute;left:84px;top:128px;font-family:"Montserrat",sans-serif;font-size:11px;font-weight:600;color:var(--charcoal);text-decoration:underline}
.card.featured{background:var(--red);border-color:var(--red)}
.card.featured h3,.card.featured p,.card.featured a{color:var(--white)}

/* about / teams */
.split{left:0;top:1267px;width:1200px;height:330px;background:linear-gradient(110deg,#9acb3e,#86c03a 60%,#95c845)}
.split .blue{position:absolute;inset:0;background:linear-gradient(120deg,#2497d6,#1a86c8 70%,#1f8fd1);clip-path:polygon(0 0,562px 0,654px 100%,0 100%)}
.split h2{position:absolute;font-family:"Montserrat",sans-serif;font-weight:600;font-size:21px;color:var(--white);display:flex;align-items:center;gap:12px;text-transform:uppercase}
.split h2 i{width:30px;height:30px;border:3px solid var(--white);border-radius:50%}
.split p{color:#f2f7fb;font-size:12px;line-height:24px}
.btn-outline{width:130px;height:45px;border:1.5px solid var(--white);color:var(--white);font-family:"Montserrat",sans-serif;font-size:11.5px;font-weight:600;display:flex;align-items:center;justify-content:center;gap:7px}
.avatar{width:90px;height:90px;border-radius:50%;border:4px solid var(--white);background:linear-gradient(#9aa1a8,#2a2f36 65%)}

/* what we do */
.work{width:330px}
.work .photo{height:206px;border:4px solid #eeeeee;outline:1px solid var(--line)}
.work h3{margin-top:30px;font-family:"Montserrat",sans-serif;font-weight:600;font-size:13.5px;color:var(--charcoal);text-transform:uppercase}
.work p{margin-top:10px;font-size:11.5px;line-height:23px}
.work a{display:flex;align-items:center;gap:6px;margin-top:16px;font-family:"Montserrat",sans-serif;font-size:11px;font-weight:600;color:var(--charcoal);text-decoration:underline}

/* partners */
.partners{left:0;top:2177px;width:1200px;height:155px;background:var(--pale)}
.partner{top:26px;width:173px;height:97px;background:var(--white);display:flex;align-items:center;justify-content:center;font-family:"Open Sans",sans-serif;font-weight:600;font-size:18px;color:#8a8a8a}
.partner .seal{width:70px;height:70px;border-radius:50%;background:#cfcfcf}

/* footer */
.footer{left:0;top:2332px;width:1200px;height:251px;background:var(--dark);color:var(--white)}
.footer h4{position:absolute;top:50px;font-family:"Montserrat",sans-serif;font-weight:600;font-size:20px}
.footer .row{position:absolute;display:flex;gap:12px;font-size:11.5px;line-height:16px;color:#e6e6e6}
.footer .row svg{flex:none;margin-top:2px}
.footer p{color:#e6e6e6;font-size:11.5px;line-height:19px}
.email-field{left:640px;top:146px;width:210px;height:34px;background:var(--white);color:#666;font-size:11.5px;padding:9px 14px}
.btn-sub{left:640px;top:190px;width:82px;height:26px;background:var(--red);color:#fff;font-size:10.5px;font-weight:600;display:flex;align-items:center;justify-content:center}
.follow{left:903px;top:168px;display:flex;gap:8px}
.follow i{width:36px;height:36px;border:1.5px solid #fff;border-radius:50%}
.copy{left:0;top:2583px;width:1200px;height:68px;background:var(--red);color:#fff;font-size:11.5px;padding:25px 0 0 387px}
</style>
</head>
<body>

<header>
  <div class="abs top-strip"><ul><li>MMJ TRASNPORT &amp; COURIER SERVICES</li><li>SURVEILLANCE AUDIT</li><li>COMPLIANCE INVESTIGATIONS</li></ul></div>
  <div class="abs brand"><i class="mark"></i><span>Harbor Crest</span></div>
  <div class="abs socials" aria-label="Social links"><i></i><i></i><i></i><i></i><i></i></div>
  <div class="abs search">Search
    <svg width="13" height="13" viewBox="0 0 13 13"><circle cx="5.5" cy="5.5" r="4" fill="none" stroke="#555" stroke-width="1.6"/><line x1="8.5" y1="8.5" x2="12" y2="12" stroke="#555" stroke-width="1.6"/></svg>
  </div>
  <nav class="abs nav"><ul>
    <li class="active">HOME</li><li>ABOUT US</li><li>OUR STAFF</li><li>OUR VEHICLES</li><li>ALARM SYSTEMS</li><li>PRIVATE INVESTIGATIONS</li><li>VIDEO SYSTEMS</li><li>VIDEO MONITORING</li><li>CONTACT US</li>
  </ul></nav>
</header>

<section>
  <div class="abs hero" role="img" aria-label="Uniformed security officer standing in front of patrol cars at dusk"></div>
  <h1 class="abs hero-title"><b>Harbor Crest</b><br>Protective Solutions</h1>
  <p class="abs hero-copy">Sed ut perspiciatis unde omnis iste natus error sit voluptatem accusantium doloremque laudantium, totam rem aperiam, eaque ipsa quae ab illo inventore quasi architecto beatae vitae dicta sunt explicabo.</p>
  <div class="abs btn-green">CLICK HERE FOR MORE INFO
    <svg width="12" height="12" viewBox="0 0 12 12"><circle cx="6" cy="6" r="5" fill="none" stroke="#fff" stroke-width="1.4"/><path d="M5 3.5 7.5 6 5 8.5" fill="none" stroke="#fff" stroke-width="1.4"/></svg></div>
  <div class="abs dots"><i></i><i></i><i class="on"></i><i></i><i></i></div>
</section>

<section>
  <h2 class="abs sec-head" style="top:742px"><i class="mark"></i>Welcome to <em>our company!</em></h2>
  <p class="abs sec-intro" style="top:795px">Sed ut perspiciatis unde omnis iste natus error sit voluptatem accusantium doloremque laudantium, totam rem aperiam, eaque ipsa quae ab illo inventore veritatis et quasi architecto beatae vitae dicta sunt explicabo.</p>

  <div class="abs card featured" style="left:85px;top:869px">
    <svg width="52" height="52" viewBox="0 0 52 52" fill="none" stroke="#fff" stroke-width="2.2"><rect x="8" y="14" width="30" height="18" rx="4" transform="rotate(-35 23 23)"/><circle cx="14" cy="38" r="5"/><circle cx="34" cy="26" r="5"/><path d="M38 8l8 6"/></svg>
    <h3>MMJ TRASNPORT</h3>
    <p>Sed ut perspiciatis unde omnis iste nat us error sit voluptatem accusantium are vitae dicta sunt explicabo.</p>
    <a>READ MORE</a>
  </div>
  <div class="abs card" style="left:436px;top:869px">
    <svg width="52" height="52" viewBox="0 0 52 52" fill="none" stroke="#777" stroke-width="2"><circle cx="22" cy="9" r="5"/><path d="M22 15l-4 14 8 6 2 12M18 29l-8 16M22 18l8 6"/><rect x="30" y="14" width="12" height="10"/></svg>
    <h3>COURIER SERVICES</h3>
    <p>Sed ut perspiciatis unde omnis iste nat us error sit voluptatem accusantium are vitae dicta sunt explicabo.</p>
    <a>READ MORE</a>
  </div>
  <div class="abs card" style="left:785px;top:869px">
    <svg width="56" height="52" viewBox="0 0 56 52" fill="none" stroke="#777" stroke-width="2"><path d="M4 30h48v-8l-8-3-6-8H18l-6 8-8 3z"/><circle cx="15" cy="32" r="5"/><circle cx="41" cy="32" r="5"/></svg>
    <h3>OUR VEHICLES</h3>
    <p>Sed ut perspiciatis unde omnis iste nat us error sit voluptatem accusantium are vitae dicta sunt explicabo.</p>
    <a>READ MORE</a>
  </div>
  <div class="abs card" style="left:85px;top:1058px">
    <svg width="52" height="52" viewBox="0 0 52 52" fill="none" stroke="#777" stroke-width="2"><path d="M12 38V24a14 14 0 0 1 28 0v14l4 4H8z"/><path d="M22 46a4 4 0 0 0 8 0M26 6v4"/></svg>
    <h3>ALARM SYSTEMS</h3>
    <p>Sed ut perspiciatis unde omnis iste nat us error sit voluptatem accusantium are vitae dicta sunt explicabo.</p>
    <a>READ MORE</a>
  </div>
  <div class="abs card" style="left:436px;top:1058px">
    <svg width="52" height="52" viewBox="0 0 52 52" fill="none" stroke="#777" stroke-width="2"><path d="M6 10l34 10-4 12L4 22z"/><path d="M24 28l-4 12H8M8 34v12"/></svg>
    <h3>VIDEO SYSTEMS</h3>
    <p>Sed ut perspiciatis unde omnis iste nat us error sit voluptatem accusantium are vitae dicta sunt explicabo.</p>
    <a>READ MORE</a>
  </div>
  <div class="abs card" style="left:785px;top:1058px">
    <svg width="52" height="52" viewBox="0 0 52 52" fill="none" stroke="#777" stroke-width="2"><rect x="4" y="8" width="44" height="30" rx="2"/><path d="M22 17l10 6-10 6z"/><path d="M18 46h16M26 38v8"/></svg>
    <h3>VIDEO MONITORING</h3>
    <p>Sed ut perspiciatis unde omnis iste nat us error sit voluptatem accusantium are vitae dicta sunt explicabo.</p>
    <a>READ MORE</a>
  </div>
</section>

<section class="abs split">
  <div class="blue"></div>
  <h2 style="left:85px;top:43px"><i></i>About us</h2>
  <div style="position:absolute;left:85px;top:99px;font-family:'Montserrat',sans-serif;font-size:13px;font-weight:500;color:#fff">TRANSPORT &amp; SECURITY SERVICES COMPANY</div>
  <p style="position:absolute;left:85px;top:134px;width:420px">Sed ut perspiciatis unde omnis iste natus error sit voluptatem accusantium doloremque laudantium, totam rem aperiam, eaque ipsa quae ab illo inventore veritatis et quasi architecto beatae vitae dicta sunt exp magni dolores eos qui ratione voluptatem</p>
  <div class="btn-outline" style="position:absolute;left:85px;top:253px">READ MORE
    <svg width="11" height="11" viewBox="0 0 12 12"><circle cx="6" cy="6" r="5" fill="none" stroke="#fff" stroke-width="1.4"/><path d="M5 3.5 7.5 6 5 8.5" fill="none" stroke="#fff" stroke-width="1.4"/></svg></div>

  <h2 style="left:698px;top:43px"><i></i>Our teams</h2>
  <p style="position:absolute;left:698px;top:106px;width:410px;text-indent:32px">Sed ut perspiciatis unde omnis iste natus error sit voluptatem accusantium doloremque laudantium, totam rem aperiam, eaque ipsa quae ab illo inventore veritatis et quasi architecto beatae vitae dicta sunt exp magni dolores eos qui ratione voluptatem</p>
  <svg style="position:absolute;left:698px;top:111px" width="20" height="14" viewBox="0 0 20 14" fill="#fff"><path d="M0 14V7l4-7h3L5 6h3v8zM11 14V7l4-7h3l-2 6h3v8z"/></svg>
  <div class="avatar" role="img" aria-label="Portrait of a team member in uniform" style="position:absolute;left:698px;top:218px"></div>
  <div style="position:absolute;left:803px;top:246px;font-family:'Montserrat',sans-serif;font-size:11.5px;font-weight:600;color:#fff">NAME : DALE ORMOND</div>
  <div style="position:absolute;left:803px;top:266px;font-size:11px;font-style:italic;color:#fff">Posted on 25 May 2016</div>
  <div style="position:absolute;left:1074px;top:253px;color:#fff;font-size:14px;letter-spacing:10px">&#8249;&#8250;</div>
</section>

<section>
  <h2 class="abs sec-head" style="top:1640px"><i class="mark"></i>What <em>we do</em></h2>
  <p class="abs sec-intro" style="top:1693px">Sed ut perspiciatis unde omnis iste natus error sit voluptatem accusantium doloremque laudantium, totam rem aperiam, eaque ipsa quae ab illo inventore veritatis et quasi architecto beatae vitae dicta sunt explicabo.</p>

  <article class="abs work" style="left:85px;top:1762px">
    <div class="photo" role="img" aria-label="Investigator looking through binoculars behind window blinds" style="background:radial-gradient(ellipse 130px 110px at 120px 120px,#a37a60,rgba(120,95,75,0) 100%),linear-gradient(115deg,#e4ddd0 0%,#c8bfae 35%,#6e6358 65%,#2f2b28 100%)"></div>
    <h3>Private Investigations</h3>
    <p>Sed ut perspiciatis unde omnis iste natus error sit volup tatem accusantium doloremque laudantium, totam rem architecto beatae vitae dicta sunt explicabo.</p>
    <a>READ MORE <svg width="10" height="10" viewBox="0 0 12 12"><circle cx="6" cy="6" r="5" fill="none" stroke="#333" stroke-width="1.4"/><path d="M5 3.5 7.5 6 5 8.5" fill="none" stroke="#333" stroke-width="1.4"/></svg></a>
  </article>
  <article class="abs work" style="left:436px;top:1762px">
    <div class="photo" role="img" aria-label="Officer in high-visibility vest beside a patrol car at night" style="background:radial-gradient(ellipse 90px 80px at 120px 150px,#c8d63a,rgba(160,170,50,0) 100%),radial-gradient(ellipse 120px 60px at 250px 40px,#3b5d9a,rgba(40,60,100,0) 100%),linear-gradient(180deg,#2f3846 0%,#242a33 60%,#1c2027 100%)"></div>
    <h3>Surveillance Audit</h3>
    <p>Sed ut perspiciatis unde omnis iste natus error sit volup tatem accusantium doloremque laudantium, totam rem architecto beatae vitae dicta sunt explicabo.</p>
    <a>READ MORE <svg width="10" height="10" viewBox="0 0 12 12"><circle cx="6" cy="6" r="5" fill="none" stroke="#333" stroke-width="1.4"/><path d="M5 3.5 7.5 6 5 8.5" fill="none" stroke="#333" stroke-width="1.4"/></svg></a>
  </article>
  <article class="abs work" style="left:785px;top:1762px">
    <div class="photo" role="img" aria-label="Hand selecting an audit tile on a digital interface" style="background:radial-gradient(ellipse 110px 90px at 180px 70px,#b9c2cc,rgba(120,130,140,0) 100%),linear-gradient(120deg,#1a1d22 0%,#4a5058 45%,#6a717a 60%,#23262b 100%)"></div>
    <h3>Compliance Investigations</h3>
    <p>Sed ut perspiciatis unde omnis iste natus error sit volup tatem accusantium doloremque laudantium, totam rem architecto beatae vitae dicta sunt explicabo.</p>
    <a>READ MORE <svg width="10" height="10" viewBox="0 0 12 12"><circle cx="6" cy="6" r="5" fill="none" stroke="#333" stroke-width="1.4"/><path d="M5 3.5 7.5 6 5 8.5" fill="none" stroke="#333" stroke-width="1.4"/></svg></a>
  </article>
</section>

<section class="abs partners">
  <svg style="position:absolute;left:44px;top:52px" width="20" height="52" viewBox="0 0 20 52"><path d="M18 2 2 26l16 24" fill="none" stroke="#cfd2d6" stroke-width="2"/></svg>
  <div class="abs partner" style="left:106px"><i class="seal"></i></div>
  <div class="abs partner" style="left:309px">Tallow</div>
  <div class="abs partner" style="left:514px">Brightfold</div>
  <div class="abs partner" style="left:717px;font-size:15px">Farspan Network</div>
  <div class="abs partner" style="left:920px">Keldmar</div>
  <svg style="position:absolute;left:1136px;top:52px" width="20" height="52" viewBox="0 0 20 52"><path d="M2 2l16 24L2 50" fill="none" stroke="#cfd2d6" stroke-width="2"/></svg>
</section>

<footer class="abs footer">
  <div style="position:absolute;left:92px;top:104px;display:flex;align-items:center;gap:12px">
    <i style="width:42px;height:42px;border-radius:50%;background:var(--red)"></i>
    <span style="font-family:'Montserrat',sans-serif;font-weight:700;font-size:26px;color:var(--red)">Harbor Crest</span>
  </div>

  <h4 style="left:390px">Contact Us</h4>
  <div class="row" style="left:390px;top:105px"><svg width="12" height="12" viewBox="0 0 12 12" fill="#fff"><path d="M1 3c0 4 4 8 8 8l2-2-2-2-1.5 1C6 7.5 4.5 6 4 4.5L5 3 3 1z"/></svg>(000)-121-1231 (Phone)</div>
  <div class="row" style="left:390px;top:133px"><svg width="12" height="12" viewBox="0 0 12 12" fill="#fff"><rect x="1" y="4" width="10" height="6"/><rect x="3" y="1" width="6" height="3"/></svg>(000)-121-1231 (Fax)</div>
  <div class="row" style="left:390px;top:161px"><svg width="12" height="12" viewBox="0 0 12 12" fill="none" stroke="#fff"><rect x="1" y="2.5" width="10" height="7"/><path d="M1 2.5l5 4 5-4"/></svg><u>info@company.com</u></div>
  <div class="row" style="left:390px;top:189px"><svg width="12" height="12" viewBox="0 0 12 12" fill="#fff"><path d="M6 0a4 4 0 0 0-4 4c0 3 4 8 4 8s4-5 4-8a4 4 0 0 0-4-4z"/></svg><span># 2548 Lorem Ipsum dummy<br>Lorem ipsum</span></div>

  <h4 style="left:640px">Newsletter Signup</h4>
  <p style="position:absolute;left:640px;top:96px;width:220px">Register Your email address to get information about us</p>
  <div class="abs email-field">Email Address</div>
  <div class="abs btn-sub">SUBSCRIBE</div>

  <h4 style="left:905px">Follow Us</h4>
  <p style="position:absolute;left:905px;top:96px;width:210px">Lorem ipsum dolor sit amet, conse ctetur adipiscing elit. Nulla in purus nibh. Donec ornare</p>
  <div class="abs follow"><i></i><i></i><i></i><i></i><i></i></div>
</footer>

<div class="abs copy">© Copyright 2016 Harbor Crest Protective solutions.All Rights Reserved</div>

</body>
</html>
```